Business Card Design - Property Management & Real Estate Services

I need a business card design for my company that I can print ZEPLA Cards. The company is called Brindle Management Company. It is a property management and real estate company. The design has to be clean and modern. I need two versions. One for my employee and one for me. However, the design will be the same, just different text. You can get a feel for the company by looking at our website at www.brindlemanagement.example.

Industry/Entity Type

Property Management

Contact Information for Business Card

I will be using ZEPLA.com to print my cards. I will most likely use the rounded edges card. I need two versions, however, they will be the same design. I need one for me and my employee.

Colors
3276b5
33a6d7

Requirements
Must have
• Company Logo
• Name of person
• Property Management & Real Estate Service
• Phone
• Email
• Website
• Address
• A space to place a QR code

```html
<!DOCTYPE html>
<html lang="en">
<head>
<meta charset="utf-8">
<title>Brindle Management Company – Business Card</title>
<link rel="stylesheet" href="https://fonts.googleapis.com/css2?family=Roboto:wght@300;400;500&display=swap">
<style>
  :root {
    --backdrop: #3a3a3c;
    --card: #1d1e22;
    --silver: #b9bcc2;
    --blue: #3276b5;
    --blue-light: #33a6d7;
    --muted: #8c8f96;
    --contact: #4f8fd0;
  }
  * { box-sizing: border-box; margin: 0; padding: 0; }
  html, body {
    width: 799px;
    height: 1200px;
    overflow: hidden;
    background: var(--backdrop);
    font-family: "Roboto", sans-serif;
  }
  .sheet {
    position: relative;
    width: 799px;
    height: 1200px;
  }
  .card {
    position: absolute;
    left: 90px;
    width: 620px;
    height: 360px;
    background: var(--card);
    border-radius: 26px;
    box-shadow: 0 14px 30px rgba(0,0,0,0.45);
  }
  .card--front { top: 110px; }
  .card--back { top: 700px; }

  .brand {
    position: absolute;
    text-align: center;
    font-weight: 400;
    line-height: 1;
  }
  .brand__name {
    display: block;
    font-size: 58px;
    letter-spacing: 4px;
  }
  .brand__sub {
    display: block;
    margin-top: 10px;
    font-size: 15px;
    letter-spacing: 12px;
  }
  .card--front .brand {
    left: 0; right: 0; top: 138px;
    color: var(--silver);
  }
  .card--back .brand {
    right: 44px; bottom: 52px;
    color: var(--blue);
  }
  .card--back .brand__name { font-size: 48px; }
  .card--back .brand__sub { font-size: 13px; letter-spacing: 10px; }

  .person {
    position: absolute;
    left: 40px; top: 36px;
  }
  .person__name {
    font-size: 19px;
    font-weight: 500;
    color: var(--blue);
  }
  .person__role {
    margin-top: 4px;
    font-size: 12px;
    color: var(--muted);
  }
  .contact {
    position: absolute;
    left: 40px; top: 168px;
    list-style: none;
    font-size: 14px;
    color: var(--contact);
    line-height: 20px;
  }
  .contact__address { padding-left: 22px; margin-bottom: 2px; }
  .contact__item {
    display: flex;
    align-items: center;
    gap: 8px;
  }
  .contact__icon {
    width: 14px; height: 14px;
    fill: none;
    stroke: var(--contact);
    stroke-width: 1.6;
    flex: none;
  }
</style>
</head>
<body>
<main class="sheet">
  <section class="card card--front" aria-label="Card front">
    <div class="brand">
      <span class="brand__name">BRINDLE</span>
      <span class="brand__sub">MANAGEMENT</span>
    </div>
  </section>

  <section class="card card--back" aria-label="Card back">
    <div class="person">
      <p class="person__name">Mateo R. Alvarez</p>
      <p class="person__role">Founder</p>
    </div>
    <ul class="contact">
      <li class="contact__address">4870 Coral Way<br>#210 Miami, FL 33199</li>
      <li class="contact__item">
        <svg class="contact__icon" viewBox="0 0 16 16"><path d="M4 2l2.5 3-1.5 1.5c1 2 2.5 3.5 4.5 4.5L11 9.5l3 2.5-1.5 2C7 13.5 2.5 9 2 3.5z"/></svg>
        (305) 555-0182
      </li>
      <li class="contact__item">
        <svg class="contact__icon" viewBox="0 0 16 16"><rect x="1.5" y="3.5" width="13" height="9"/><path d="M1.5 3.5l6.5 5 6.5-5"/></svg>
        mateo@brindlemanagement.example
      </li>
      <li class="contact__item">
        <svg class="contact__icon" viewBox="0 0 16 16"><circle cx="8" cy="8" r="6.5"/><ellipse cx="8" cy="8" rx="2.8" ry="6.5"/><path d="M1.5 8h13"/></svg>
        www.brindlemanagement.example
      </li>
    </ul>
    <div class="brand">
      <span class="brand__name">BRINDLE</span>
      <span class="brand__sub">MANAGEMENT</span>
    </div>
  </section>
</main>
</body>
</html>
```